Moravel Aesthetic Doctor

I require an elegant, luxurious looking business card for my aesthetic business. I am a doctor and that will set me aside from competitors. I am planning to provide home and spa based treatments to clients with high expectations. I have attached my logo.

```html
<!DOCTYPE html>
<html lang="en">
<head>
<meta charset="utf-8">
<title>Moravel Aesthetic Doctor – Business Card</title>
<link href="https://fonts.googleapis.com/css2?family=Montserrat:wght@400;600&display=swap" rel="stylesheet">
<style>
  :root{
    --page:#eceeef;
    --card-grey:#a4a6a8;
    --sky:#7dccf0;
    --sky-deep:#4fb3e6;
    --ink-grey:#8f9295;
    --white:#ffffff;
    --shadow:rgba(0,0,0,.18);
  }
  *{box-sizing:border-box;margin:0;padding:0}
  html,body{width:1200px;height:1124px;overflow:hidden;background:var(--page);font-family:"Montserrat",sans-serif}
  .card{position:absolute;left:180px;width:840px;height:480px;box-shadow:0 6px 18px var(--shadow);overflow:hidden}
  .card-back{top:60px;background:var(--card-grey);color:var(--white)}
  .card-front{top:584px;background:var(--white)}

  /* brand block */
  .brand{position:absolute;display:flex;align-items:center;gap:20px;white-space:nowrap}
  .brand-dot{width:84px;height:84px;border-radius:50%;border:3px solid currentColor;flex:none}
  .brand-name{font-weight:400;line-height:1}
  .brand-name .word{display:block;font-size:54px;letter-spacing:3px}
  .brand-name .sub{display:block;font-size:19px;letter-spacing:3px;margin-top:8px;text-transform:uppercase}

  .card-back .brand{left:0;right:0;top:112px;justify-content:center;color:var(--white)}
  .services{position:absolute;left:0;right:0;top:290px;text-align:center;font-size:21px;line-height:1.5;letter-spacing:.3px}

  .card-front .brand{right:70px;top:196px;color:var(--ink-grey)}
  .band{position:absolute;left:0;top:0;width:840px;height:180px}
  .holder{position:absolute;left:60px;top:26px;color:var(--white)}
  .holder-name{font-weight:600;font-size:25px}
  .holder-name small{font-size:15px;margin-left:4px}
  .holder-title{font-size:19px;margin-top:6px}

  .contact{position:absolute;left:60px;top:318px;list-style:none;color:var(--ink-grey);font-size:21px}
  .contact li{display:flex;align-items:center;gap:14px;height:34px;white-space:nowrap}
  .contact svg{width:18px;height:18px;flex:none}
  .contact .hl{color:var(--sky-deep)}

  .social{position:absolute;right:70px;bottom:44px;display:flex;gap:22px}
  .social span{width:30px;height:30px;border-radius:50%;background:var(--sky)}
</style>
</head>
<body>

<section class="card card-back" aria-label="Card back">
  <div class="brand">
    <span class="brand-dot"></span>
    <div class="brand-name"><span class="word">MORAVEL</span><span class="sub">Aesthetic Doctor</span></div>
  </div>
  <p class="services">
    Dermal injectables • Plasma facials • Microneedling<br>
    Skin boosters • Excessive sweating<br>
    Home and Spa Based Treatments
  </p>
</section>

<section class="card card-front" aria-label="Card front">
  <svg class="band" viewBox="0 0 840 180" aria-hidden="true">
    <polygon points="0,0 840,0 840,150 580,150 600,130 0,118" fill="var(--sky)"/>
    <polygon points="0,100 610,112 590,130 0,118" fill="var(--white)"/>
    <polygon points="0,118 600,130 580,150 840,150 840,158 0,128" fill="var(--sky)"/>
    <polygon points="640,140 840,146 840,160 625,168" fill="var(--ink-grey)" opacity=".8"/>
  </svg>
  <div class="holder">
    <p class="holder-name">Dr Elise Varden, <small>MRCPCH MD</small></p>
    <p class="holder-title">Australasian Diploma of Aesthetic Medicine</p>
  </div>

  <div class="brand">
    <span class="brand-dot"></span>
    <div class="brand-name"><span class="word">MORAVEL</span><span class="sub">Aesthetic Doctor</span></div>
  </div>

  <ul class="contact">
    <li><svg viewBox="0 0 24 24"><path d="M6 2l4 4-2 3c1 3 4 6 7 7l3-2 4 4-3 4C10 22 2 14 2 5z" fill="var(--sky-deep)"/></svg><span>0800 555 014</span></li>
    <li><svg viewBox="0 0 24 24"><rect x="2" y="5" width="20" height="14" fill="none" stroke="var(--sky-deep)" stroke-width="2"/><path d="M2 5l10 8 10-8" fill="none" stroke="var(--sky-deep)" stroke-width="2"/></svg><span>elise@moravel.co.nz</span></li>
    <li><svg viewBox="0 0 24 24"><circle cx="12" cy="12" r="10" fill="none" stroke="var(--sky-deep)" stroke-width="2"/><path d="M2 12h20M12 2c-5 6-5 14 0 20M12 2c5 6 5 14 0 20" fill="none" stroke="var(--sky-deep)" stroke-width="2"/></svg><span>www.<span class="hl">moravel</span>.co.nz</span></li>
  </ul>

  <div class="social" aria-hidden="true"><span></span><span></span></div>
</section>

</body>
</html>
```